Web design project for exciting Australian start-up

Background
We are looking for a creative and talented web design artist to work alongside our market leading web developer.
• You will be required to create a modern and clean design theme for our website, incorporating selected rustic colour scheme elements for our exciting Australian start-up to operate within the coffee industry.
reoccurring work to be expected to flow to the successful designer.
Requirements
• c. 5 - 10 page website
• Landing page
• Log in/ out
• 404 template
• Typography is emphasised
• Please use either a) typemarrow.com, b) free web fonts, c) brindle fonts
• All design elements in vector format
• Preferably with icons for each header title(i.e. about us, how it works etc) but designer have free reign over how the site looks, so might not be applicable
• All pages to be responsive
• Down to eSlab resolution

High level visual design brief attached - additional pages to be worked from base design.

Design inspiration
• We would like to use design elements from the following sources:
http://www.zandrix.com/halcyon/ (Functionality)
Colour scheme refer to logo and complementary style guide

```html
<!DOCTYPE html>
<html lang="en">
<head>
<meta charset="utf-8">
<title>Brewline – Marketplace</title>
<link href="https://fonts.googleapis.com/css2?family=Open+Sans:wght@300;400;600;700&display=swap" rel="stylesheet">
<style>
:root{
  --orange:#dea050;
  --orange-light:#f0b567;
  --orange-text:#e0a04f;
  --orange-deep:#b8660f;
  --title-red:#c0282d;
  --grey-bg:#e6e6e6;
  --grey-line:#dcdcdc;
  --text:#333;
  --text-soft:#777;
  --star-dark:#333;
  --footer-bar:#4b4c4a;
  --white:#fff;
}
*{box-sizing:border-box;margin:0;padding:0}
html,body{width:1200px;height:1112px;overflow:hidden}
body{position:relative;background:var(--white);font-family:"Open Sans",sans-serif;color:var(--text)}
.abs{position:absolute}
.site-header{position:absolute;left:0;top:0;width:1200px;height:134px;border-bottom:3px solid var(--orange-light)}
.brand{position:absolute;left:113px;top:38px;display:flex;align-items:center;gap:14px;font-size:34px;font-weight:700;color:#222;letter-spacing:2px}
.brand-dot{width:44px;height:44px;border-radius:50%;background:var(--orange)}
.btn{position:absolute;height:37px;line-height:37px;text-align:center;color:var(--white);font-size:14px;font-weight:600;background:var(--orange);border:1px solid #e9c08b}
.btn-light{background:var(--orange-light)}
.page-title{left:108px;top:150px;font-size:30px;font-weight:400;color:var(--orange-text)}
.chip{position:absolute;top:208px;height:46px;line-height:46px;text-align:center;font-size:14px;font-weight:600;color:#444;background:var(--grey-bg);border-radius:2px}
.chip-active{background:var(--orange-light);color:var(--white)}
.quantity{left:806px;width:258px;background:linear-gradient(#f4f4f4,#e2e2e2);border:1px solid #ddd}
.quantity span{color:var(--orange-deep)}
.search-bar{left:110px;top:273px;width:955px;height:49px;border:1px solid var(--grey-line);font-size:14px}
.search-bar .cell{position:absolute;top:0;height:47px;display:flex;align-items:center;gap:10px;border-right:1px solid var(--grey-line)}
.sort-label{position:absolute;left:629px;top:15px;font-size:13px;color:#555}
.sort-select{position:absolute;left:668px;top:7px;width:136px;height:33px;background:#eee;border:1px solid #ddd;font-size:13px;line-height:31px;padding-left:9px}
.sort-select::after{content:"";position:absolute;right:9px;top:13px;border:6px solid transparent;border-top:7px solid #888}
.view-label{position:absolute;left:818px;top:15px;font-size:13px;color:#555}
.view-switch{position:absolute;left:859px;top:7px;width:83px;height:33px;background:#eee;border:1px solid #ddd;display:flex;align-items:center;justify-content:space-around;padding:0 5px}
.results-title{left:119px;top:366px;font-size:22px;color:var(--orange-text)}
.card{position:absolute;left:120px;width:931px;height:168px;border:1px solid var(--grey-line)}
.card .logo{position:absolute;left:0;top:0;width:210px;height:166px;border-right:1px solid var(--grey-line);display:flex;align-items:center;justify-content:center}
.logo-mark{width:150px;height:100px;border-radius:6px;display:flex;align-items:center;justify-content:center;font-size:15px;font-weight:600}
.card .info{position:absolute;left:227px;top:25px;font-size:13px}
.bean-name{color:#d98b2c;font-size:14px;margin-bottom:17px}
.card-2 .bean-name{color:var(--title-red)}
.info .label{color:var(--text-soft);margin-bottom:7px}
.info .row{display:flex;margin-bottom:4px}
.info .row b{font-weight:400;width:108px}
.card .reviews{position:absolute;left:611px;top:0;width:318px;height:166px;border-left:1px solid var(--grey-line)}
.reviews-head{position:absolute;left:10px;top:20px;display:flex;align-items:center;gap:18px;color:var(--orange-deep);font-size:14px}
.rating-label{position:absolute;left:19px;top:53px;font-size:13px;color:var(--text-soft);line-height:18px}
.stars{position:absolute;left:174px;top:54px;display:flex;gap:5px}
.offer-label{position:absolute;left:19px;top:113px;font-size:13px;color:var(--text-soft)}
.offer-icons{position:absolute;left:130px;top:108px;display:flex;gap:16px}
.ribbon{position:absolute;top:845px;height:30px;line-height:30px;padding-left:11px;font-size:15px;color:#444;background:var(--grey-bg);clip-path:polygon(0 0,100% 0,calc(100% - 8px) 50%,100% 100%,0 100%)}
.link-list{position:absolute;top:895px;list-style:none;font-size:12px;color:#444;line-height:22px}
.social{position:absolute;left:888px;top:886px;list-style:none}
.social li{display:flex;align-items:center;height:38px;font-size:12px;color:#666;gap:9px}
.social li strong{font-weight:400;font-size:14px;color:#777;margin-left:2px}
.social-box{width:26px;height:26px;background:linear-gradient(#9a9a9a,#5c5c5c);border-radius:2px}
.site-footer{position:absolute;left:0;top:1050px;width:1200px;height:62px;background:var(--footer-bar);color:var(--white);font-size:13px}
.copyright{position:absolute;left:420px;top:26px}
.page-code{position:absolute;left:1157px;top:26px}
</style>
</head>
<body>

<header class="site-header">
  <div class="brand"><span>BREWLINE</span><span class="brand-dot"></span></div>
  <a class="btn" style="left:714px;top:40px;width:143px">My Account</a>
  <a class="btn btn-light" style="left:877px;top:40px;width:98px">Loggedin</a>
  <a class="btn" style="left:975px;top:40px;width:103px">Logout</a>
</header>

<h1 class="abs page-title">MARKETPLACE</h1>

<div class="chip" style="left:109px;width:162px">TENDER FORMAT &nbsp;:</div>
<div class="chip chip-active" style="left:280px;width:62px">ALL</div>
<div class="chip" style="left:350px;width:92px">ONE-OFF</div>
<div class="chip" style="left:451px;width:102px">RECURRING</div>
<div class="chip quantity"><span>QUANTITY (KG) :</span> &nbsp;35 KG/WEEK</div>

<div class="abs search-bar">
  <div class="cell" style="left:0;width:211px;padding-left:19px">
    <svg width="10" height="10" viewBox="0 0 10 10"><path d="M1 1L9 9M9 1L1 9" stroke="#999" stroke-width="2.4"/></svg>
    <span>Results for Café Marlo</span>
  </div>
  <div class="cell" style="left:211px;width:145px;padding-left:17px">
    <svg width="18" height="17" viewBox="0 0 24 23"><path d="M12 0l3.6 7.6 8.4 1-6.2 5.8 1.6 8.3L12 18.6l-7.4 4.1 1.6-8.3L0 8.6l8.4-1z" fill="#888"/></svg>
    <span>Save search</span>
  </div>
  <span class="sort-label">Sort :</span>
  <div class="sort-select">Highest rated</div>
  <span class="view-label">View :</span>
  <div class="view-switch">
    <svg width="11" height="11"><rect width="5" height="5" fill="#666"/><rect x="6" width="5" height="5" fill="#666"/><rect y="6" width="5" height="5" fill="#666"/><rect x="6" y="6" width="5" height="5" fill="#666"/></svg>
    <svg width="11" height="11" fill="#666"><rect width="3" height="3"/><rect x="4" width="3" height="3"/><rect x="8" width="3" height="3"/><rect y="4" width="3" height="3"/><rect x="4" y="4" width="3" height="3"/><rect x="8" y="4" width="3" height="3"/><rect y="8" width="3" height="3"/><rect x="4" y="8" width="3" height="3"/><rect x="8" y="8" width="3" height="3"/></svg>
    <svg width="12" height="11" fill="#666"><rect width="3" height="3"/><rect x="4" width="8" height="3"/><rect y="4" width="3" height="3"/><rect x="4" y="4" width="8" height="3"/><rect y="8" width="3" height="3"/><rect x="4" y="8" width="8" height="3"/></svg>
  </div>
</div>

<h2 class="abs results-title" style="font-weight:400">RESULTS</h2>

<svg width="0" height="0" style="position:absolute">
  <defs>
    <symbol id="star" viewBox="0 0 24 23"><path d="M12 0l3.6 7.6 8.4 1-6.2 5.8 1.6 8.3L12 18.6l-7.4 4.1 1.6-8.3L0 8.6l8.4-1z"/></symbol>
    <symbol id="bubble" viewBox="0 0 40 24"><ellipse cx="20" cy="10" rx="19" ry="9.5"/><path d="M10 16l-3 8 10-6z"/></symbol>
    <symbol id="cup" viewBox="0 0 30 30"><path d="M10 2c-2 3 2 4 0 7M15 2c-2 3 2 4 0 7" stroke="#555" stroke-width="1.6" fill="none"/><path d="M4 12h18v6a7 7 0 0 1-7 7h-4a7 7 0 0 1-7-7z" fill="#555"/><path d="M22 14h2a3 3 0 0 1 0 6h-2" stroke="#555" stroke-width="2" fill="none"/><rect x="2" y="26" width="24" height="2" fill="#555"/></symbol>
    <symbol id="cap" viewBox="0 0 30 30"><path d="M15 6L1 13l14 7 14-7z" fill="#555"/><path d="M7 17v5c4 3 12 3 16 0v-5l-8 4z" fill="#555"/><rect x="26" y="14" width="1.6" height="9" fill="#555"/></symbol>
    <symbol id="takeaway" viewBox="0 0 30 30"><rect x="6" y="2" width="18" height="4" fill="#555"/><path d="M7 7h16l-2 21H9z" fill="#555"/><circle cx="15" cy="16" r="4" fill="#fff"/></symbol>
    <symbol id="horn" viewBox="0 0 30 30"><path d="M24 4v20L12 19H6v-9h6z" fill="#555"/><rect x="2" y="10" width="3" height="9" fill="#555"/><path d="M8 20l2 7h3l-1-7z" fill="#555"/></symbol>
  </defs>
</svg>

<article class="card card-1" style="top:409px">
  <div class="logo">
    <div class="logo-mark" role="img" aria-label="Harlow Roasters supplier logo" style="background:#efe3d6;color:#7a2b22">Harlow Roasters</div>
  </div>
  <div class="info">
    <h3 class="bean-name" style="font-weight:400">Coffee bean XX</h3>
    <p class="label">Blend description :</p>
    <p class="row"><b>Origin</b>: &nbsp;&nbsp;[xx]</p>
    <p class="row"><b>Grind availability</b>: &nbsp;&nbsp;[xx]</p>
  </div>
  <div class="reviews">
    <div class="reviews-head"><svg width="40" height="24" fill="#dea050"><use href="#bubble"/></svg>Reviews for this bean :</div>
    <p class="rating-label">Wholesaler's overall<br>customer rating :</p>
    <div class="stars">
      <svg width="16" height="15" fill="#e5a14d"><use href="#star"/></svg><svg width="16" height="15" fill="#e5a14d"><use href="#star"/></svg><svg width="16" height="15" fill="#e5a14d"><use href="#star"/></svg><svg width="16" height="15" fill="#e5a14d"><use href="#star"/></svg><svg width="16" height="15" fill="#333"><use href="#star"/></svg>
    </div>
    <p class="offer-label">Other offerings</p>
    <div class="offer-icons">
      <svg width="30" height="30"><use href="#cup"/></svg><svg width="30" height="30"><use href="#cap"/></svg><svg width="30" height="30"><use href="#takeaway"/></svg><svg width="30" height="30"><use href="#horn"/></svg>
    </div>
  </div>
</article>

<article class="card card-2" style="top:610px">
  <div class="logo">
    <div class="logo-mark" role="img" aria-label="Fieldmate Beans supplier logo" style="background:#eef3e6;color:#3d2f28">Fieldmate Beans</div>
  </div>
  <div class="info">
    <h3 class="bean-name" style="font-weight:400">Coffee bean XX</h3>
    <p class="label">Blend description :</p>
    <p class="row"><b>Origin</b>: &nbsp;&nbsp;[xx]</p>
    <p class="row"><b>Grind availability</b>: &nbsp;&nbsp;[xx]</p>
  </div>
  <div class="reviews">
    <div class="reviews-head"><svg width="40" height="24" fill="#dea050"><use href="#bubble"/></svg>Reviews for this bean :</div>
    <p class="rating-label">Wholesaler's overall<br>customer rating :</p>
    <div class="stars">
      <svg width="16" height="15" fill="#e5a14d"><use href="#star"/></svg><svg width="16" height="15" fill="#e5a14d"><use href="#star"/></svg><svg width="16" height="15" fill="#e5a14d"><use href="#star"/></svg><svg width="16" height="15" fill="#e5a14d"><use href="#star"/></svg><svg width="16" height="15" fill="#333"><use href="#star"/></svg>
    </div>
    <p class="offer-label">Other offerings</p>
    <div class="offer-icons">
      <svg width="30" height="30"><use href="#cup"/></svg><svg width="30" height="30"><use href="#cap"/></svg><svg width="30" height="30"><use href="#takeaway"/></svg><svg width="30" height="30"><use href="#horn"/></svg>
    </div>
  </div>
</article>

<div class="ribbon" style="left:126px;width:124px">Helpful info</div>
<ul class="link-list" style="left:139px">
  <li>About us</li><li>Media enquiries</li><li>Terms &amp; conditions</li><li>Privacy policy</li>
</ul>

<div class="ribbon" style="left:337px;width:124px">Who we are</div>
<ul class="link-list" style="left:350px">
  <li>How it works</li><li>FAQ</li><li>Contact us</li>
</ul>

<div class="ribbon" style="left:888px;width:192px;padding-left:19px;top:844px">Connect with us</div>
<ul class="social">
  <li><span class="social-box"></span>Join with us on <strong>Friendwall</strong></li>
  <li><span class="social-box"></span>Follow us on <strong>Chirper</strong></li>
  <li><span class="social-box"></span>Share on <strong>Worklink</strong></li>
  <li><span class="social-box"></span>Watch on <strong>Vidstream</strong></li>
</ul>

<footer class="site-footer">
  <span class="copyright">© 2014 Brewline. &nbsp; All rights reserved.</span>
  <span class="page-code">X2</span>
</footer>

</body>
</html>
```